Corvo Splendia

I want a glossy card on both sides. We sell underwater LED lights for water craft

we sell custom audio enclosures for automobile, boats and atv's.

view our websites for any other pictures you may think are better suited.

Industry/Entity Type

Audio

Contact Information for Business Card

Email address: CorvoSplendia@mailpost.test
Website: www.hullglowbeam.test
underwater LED lighting for watercraft
boat drain plug lights
phone number: 555-271-0846

other side of card:
email address the same
website: www.genericsoundhousings.test
speaker enclosures, auto, boat and atv
same phone number

```html
<!DOCTYPE html>
<html lang="en">
<head>
<meta charset="utf-8">
<title>Underwater LED Lights – Business Cards</title>
<link href="https://fonts.googleapis.com/css2?family=Audiowide&family=Open+Sans:wght@400;600&display=swap" rel="stylesheet">
<style>
  :root {
    --page: #e6e6e6;
    --night: #14161b;
    --night-soft: #1d2129;
    --lime: #a4cc2c;
    --ocean: #1c5b95;
    --title: #d8dadf;
    --ink-dark: #1b1e22;
    --ink-light: #ffffff;
  }
  * { box-sizing: border-box; margin: 0; padding: 0; }
  html, body { width: 1200px; height: 1200px; overflow: hidden; }
  body {
    background: var(--page);
    font-family: "Open Sans", sans-serif;
    position: relative;
  }
  .card {
    position: absolute;
    left: 150px;
    width: 900px;
    height: 514px;
    overflow: hidden;
    box-shadow: 0 6px 18px rgba(0,0,0,0.18);
  }
  .card--lights { top: 60px; background: var(--lime); }
  .card--audio { top: 626px; background: var(--ocean); }

  .card__band {
    position: absolute;
    left: 0; top: 0;
    width: 100%; height: 250px;
    background: var(--night);
  }
  .card--lights .card__band {
    background:
      radial-gradient(ellipse 220px 90px at 230px 40px, rgba(42,127,224,0.85), transparent 70%),
      radial-gradient(ellipse 160px 60px at 700px 190px, rgba(31,165,154,0.45), transparent 70%),
      var(--night);
  }
  .card--audio .card__band {
    background:
      linear-gradient(160deg, rgba(30,110,140,0.35), transparent 55%),
      var(--night-soft);
  }

  .card__title {
    position: absolute;
    left: 160px; top: 118px;
    width: 700px;
    font-family: "Audiowide", sans-serif;
    font-size: 38px;
    font-weight: 400;
    letter-spacing: 2px;
    line-height: 1.2;
    color: var(--title);
    white-space: nowrap;
  }
  .card__subtitle {
    position: absolute;
    left: 330px; top: 172px;
    font-size: 20px;
    color: var(--title);
    letter-spacing: 0.5px;
  }

  .photo-grid {
    position: absolute;
    left: 40px; top: 262px;
    width: 290px; height: 226px;
    display: grid;
    grid-template-columns: 1fr 1fr;
    grid-template-rows: 1fr 1fr;
    gap: 6px;
    background: var(--ink-dark);
    padding: 6px;
  }
  .photo-grid__cell--a { background: radial-gradient(circle at 40% 60%, #2b6a8a, #0c1116 70%); }
  .photo-grid__cell--b { background: linear-gradient(180deg, #405c8a, #c98b6a 55%, #1d2436); }
  .photo-grid__cell--c { background: radial-gradient(circle at 50% 60%, #3fb36a, #0d1a14 70%); }
  .photo-grid__cell--d { background: radial-gradient(circle at 50% 55%, #3a4fd0, #0a0c20 70%); }

  .product-photo {
    position: absolute;
    border-radius: 50%;
    background: radial-gradient(circle at 45% 45%, #b8bcc2, #5d6168 45%, #121317 75%);
  }
  .product-photo--large { left: 30px; top: 240px; width: 250px; height: 250px; }
  .product-photo--small { left: 40px; top: 8px; width: 105px; height: 105px; }
  .product-photo--dome {
    left: 700px; top: 14px; width: 170px; height: 92px;
    border-radius: 50% 50% 40% 40%;
    background: radial-gradient(ellipse at 50% 30%, #4a4d54, #0b0c0f 70%);
  }

  .contact {
    position: absolute;
    left: 430px; top: 290px;
    list-style: none;
  }
  .contact__item {
    display: flex;
    align-items: center;
    gap: 14px;
    font-size: 26px;
    line-height: 1.55;
    white-space: nowrap;
  }
  .contact__item--phone { font-size: 36px; font-weight: 600; }
  .contact__icon { width: 22px; height: 22px; flex: none; }
  .card--lights .contact__item { color: var(--ink-dark); }
  .card--lights .contact__icon { fill: var(--ink-dark); }
  .card--audio .contact__item { color: var(--ink-light); }
  .card--audio .contact__icon { fill: var(--ink-light); }
</style>
</head>
<body>

<section class="card card--lights">
  <div class="card__band" role="img" aria-label="Photo of boats glowing with blue and teal underwater lights at night"></div>
  <h1 class="card__title">UNDERWATER LED LIGHTS</h1>
  <p class="card__subtitle">FOR WATER CRAFT</p>
  <div class="photo-grid">
    <div class="photo-grid__cell--a" role="img" aria-label="Boat lit underwater at night"></div>
    <div class="photo-grid__cell--b" role="img" aria-label="Boat on the water at sunset"></div>
    <div class="photo-grid__cell--c" role="img" aria-label="Green underwater light glow"></div>
    <div class="photo-grid__cell--d" role="img" aria-label="Blue drain plug light shining"></div>
  </div>
  <ul class="contact">
    <li class="contact__item contact__item--phone">
      <svg class="contact__icon" viewBox="0 0 24 24"><rect x="6" y="1" width="12" height="22" rx="2"/></svg>555-271-0846
    </li>
    <li class="contact__item">
      <svg class="contact__icon" viewBox="0 0 24 24"><rect x="2" y="6" width="20" height="12" rx="2"/></svg>CorvoSplendia@mailpost.test
    </li>
    <li class="contact__item">
      <svg class="contact__icon" viewBox="0 0 24 24"><circle cx="12" cy="12" r="10"/></svg>www.hullglowbeam.test
    </li>
  </ul>
</section>

<section class="card card--audio">
  <div class="card__band" role="img" aria-label="Dark background with blue light streak lines"></div>
  <div class="product-photo product-photo--small" role="img" aria-label="Speaker pod product photo"></div>
  <div class="product-photo product-photo--dome" role="img" aria-label="Black speaker enclosure product photo"></div>
  <h1 class="card__title">UNDERWATER LED LIGHTS</h1>
  <p class="card__subtitle">FOR WATER CRAFT</p>
  <div class="product-photo product-photo--large" role="img" aria-label="Speaker enclosure with chrome grille and tweeter"></div>
  <ul class="contact">
    <li class="contact__item contact__item--phone">
      <svg class="contact__icon" viewBox="0 0 24 24"><rect x="6" y="1" width="12" height="22" rx="2"/></svg>555-271-0846
    </li>
    <li class="contact__item">
      <svg class="contact__icon" viewBox="0 0 24 24"><rect x="2" y="6" width="20" height="12" rx="2"/></svg>CorvoSplendia@mailpost.test
    </li>
    <li class="contact__item">
      <svg class="contact__icon" viewBox="0 0 24 24"><circle cx="12" cy="12" r="10"/></svg>www.hullglowbeam.test
    </li>
  </ul>
</section>

</body>
</html>
```